The World Most Wanted Eyelahes

1. We need a web design for a new company based in California, USA
2. We are the manufacturer for 100% human hair eyelashes,
made in Indonesia.
3. We recently launched "Tapered Eyelashes" with human hair.
Currently, none of the people carried Tapered eyelash.
4. We would like to see designs that use the 4 different colors that match with my products as "Four Seasons" concepts.
5. We prefer to follow www.pelvo.com style, like professional website.
6. Focus on products as a manufacturer, therefore, all wholesaler and retailer copy and paste to their marketing tools.
7. Need bilingual English and Spanish.
8. Easy to link with social media.

Target Market(s)

United States and Central/South America.

Industry/Entity Type

Hair

Number of Pages Required

5+ page

Requirements
Must have
• 1. Details of Products with image.
• 2. Hottest/Newest Items "Tapered in 100% Human Hair"
• 3. Store Page
Nice to have
• 1. My competitors is Quorim Eyelash. http://www.quorimlashes.com/
• Please follow the concepts of it.
• 2. www.Pelvo.com: They have great products detail on the website.
• i would like to focus on "Tapered" for new styles of the eyelash.
• 3. I want to visitors can write down the "Reviews" in every single product.
• Please check the www.QTRCosmetics.com.
Should not have
• It's not salon/Shop for the beauty.
• No need an appointment.
• We are the manufacturer of the eyelash.

```html
<!DOCTYPE html>
<html lang="en">
<head>
<meta charset="utf-8">
<title>Lumiqa Eyelashes</title>
<link href="https://fonts.googleapis.com/css2?family=Lato:wght@400;700&family=Great+Vibes&family=Playfair+Display:ital,wght@1,700&display=swap" rel="stylesheet">
<style>
:root{
  --gold:#b8802e;
  --dark:#2b2b2b;
  --nav:#333;
  --text:#222;
  --muted:#444;
  --rose:#d4626a;
  --rose-btn:#a9373f;
  --magenta:#c02aa0;
  --magenta-btn:#8c1a74;
  --mustard:#e2b92e;
  --mustard-btn:#b38f1a;
  --sky:#8ebdd6;
  --sky-btn:#5f93b0;
  --footer:#ececec;
}
*{margin:0;padding:0;box-sizing:border-box}
html,body{width:800px;height:1200px;overflow:hidden;background:#fff}
body{font-family:"Lato",sans-serif;color:var(--text);position:relative}
.abs{position:absolute}
.topline{left:0;top:0;width:800px;height:2px;background:linear-gradient(90deg,#e9a3a8 0 25%,#c02aa0 25% 50%,#e2b92e 50% 75%,#8ebdd6 75%)}
.logo{left:66px;top:18px;display:flex;align-items:center;gap:6px}
.logo-mark{width:10px;height:10px;background:var(--gold)}
.logo-name{font-size:30px;color:var(--gold);font-weight:400;letter-spacing:1px;line-height:1}
.logo-sub{left:66px;top:52px;font-size:8px;letter-spacing:3px;color:var(--dark)}
.lang{left:342px;top:29px;width:88px;height:19px;border:1px solid #999;font-size:6px;display:flex;align-items:center;justify-content:center;gap:3px}
.flag{width:8px;height:5px;background:linear-gradient(#b22 0 50%,#fff 50%);border:0.5px solid #36c}
.cart{top:13px;font-size:7px;display:flex;align-items:center;gap:6px}
.cart svg{width:13px;height:13px}
.sep{left:646px;top:11px;width:1px;height:16px;background:#ccc}
.search{left:542px;top:40px;width:192px;height:22px;background:#f2f2f2}
.search-btn{left:709px;top:40px;width:25px;height:22px;background:var(--dark);display:flex;align-items:center;justify-content:center}
.nav{left:66px;top:73px;width:668px;height:27px;display:flex;background:var(--nav)}
.nav a{color:#fff;font-size:9px;text-decoration:none;display:flex;align-items:center;justify-content:center;border-right:1px solid #555}
.nav a.active{background:var(--gold)}
.hero{left:66px;top:110px;width:668px;height:286px;background:linear-gradient(90deg,#c7a49a 0%,#8a5b6e 22%,#3d3a3b 48%,#2f3130 100%)}
.hero-title{left:413px;top:198px;font-family:"Great Vibes",cursive;color:#fff;font-size:31px;line-height:38px;width:290px}
.arrow{top:236px;width:20px;height:20px;border-radius:50%;display:flex;align-items:center;justify-content:center}
.h2{width:800px;text-align:center;font-size:14px;color:var(--text)}
.intro{left:76px;top:440px;width:648px;font-size:7.4px;line-height:10.6px;text-align:center;color:var(--muted)}
.features{left:66px;top:509px;width:670px;display:flex;justify-content:space-between}
.feature{display:flex;gap:10px;font-size:7.8px;line-height:10px;width:134px}
.feature svg{flex:none;width:11px;height:11px;margin-top:0}
.cards{left:66px;top:598px;display:flex;gap:12.6px}
.card{width:158px;height:185px;padding:6px 7px;text-align:center}
.card .photo{width:144px;height:124px}
.card h3{font-weight:400;color:#fff;font-size:13px;margin-top:8px}
.card .more{display:inline-block;width:62px;height:15px;margin-top:4px;font-size:9px;color:#fff;line-height:15px}
.rose{background:var(--rose)} .rose .more{background:var(--rose-btn)}
.magenta{background:var(--magenta)} .magenta .more{background:var(--magenta-btn)}
.mustard{background:var(--mustard)} .mustard .more{background:var(--mustard-btn)}
.sky{background:var(--sky)} .sky .more{background:var(--sky-btn)}
.banner{left:66px;top:824px;width:668px;height:87px;background:linear-gradient(90deg,#fbf7ef 0%,#f6efe3 60%,#e9d9c8 80%,#c9b09c 100%)}
.banner-text{left:118px;top:846px;font-family:"Playfair Display",serif;font-style:italic;font-weight:700;font-size:12.5px;line-height:21px;color:#3a2f28}
.banner-text b{color:var(--gold);font-size:17px}
.footer{left:0;top:950px;width:800px;height:250px;background:var(--footer)}
.fcol h4{font-weight:400;font-size:14px;color:var(--text);margin-bottom:19px}
.fcol ul{list-style:none;font-size:7.8px;line-height:13.6px;color:var(--muted)}
.news-input{left:518px;top:1018px;width:216px;height:40px;background:#fff;border:1px solid #ddd;font-size:8px;display:flex;align-items:center;justify-content:center}
.news-btn{left:518px;top:1059px;width:216px;height:29px;background:#222;color:#fff;font-size:10px;display:flex;align-items:center;justify-content:center}
.social{left:518px;top:1124px;display:flex;gap:4.5px}
.social span{width:20px;height:20px}
.rule{left:0;top:1164px;width:800px;height:1px;background:#ddd}
.copy{left:0;top:1178px;width:800px;text-align:center;font-size:7.5px;color:var(--muted)}
</style>
</head>
<body>
<div class="abs topline"></div>

<div class="abs logo"><span class="logo-mark"></span><span class="logo-name">LUMIQA</span></div>
<div class="abs logo-sub">EYELASHES</div>

<div class="abs lang"><span class="flag"></span>Language: English ˅</div>

<div class="abs cart" style="left:570px">Cart (Empty)
  <svg viewBox="0 0 14 14"><circle cx="7" cy="4" r="3" fill="#b8802e"/><path d="M1 14c0-4 3-6 6-6s6 2 6 6z" fill="#b8802e"/></svg>
</div>
<div class="abs sep"></div>
<div class="abs cart" style="left:662px">Cart (Empty)
  <svg viewBox="0 0 14 14"><path d="M1 2h2l2 7h7l1.5-5H4" fill="none" stroke="#b8802e" stroke-width="1.4"/><circle cx="6" cy="12" r="1.2" fill="#b8802e"/><circle cx="11" cy="12" r="1.2" fill="#b8802e"/></svg>
</div>

<div class="abs search"></div>
<div class="abs search-btn"><svg width="11" height="11" viewBox="0 0 12 12"><circle cx="5" cy="5" r="3.6" fill="none" stroke="#fff" stroke-width="1.4"/><path d="M7.7 7.7L11 11" stroke="#fff" stroke-width="1.4"/></svg></div>

<nav class="abs nav">
  <a class="active" style="width:106px">Home</a>
  <a style="width:99px">About Us</a>
  <a style="width:98px">Services</a>
  <a style="width:126px">Our Products</a>
  <a style="width:121px">Testimonials</a>
  <a style="width:118px;border:0">Contact Us</a>
</nav>

<div class="abs hero" role="img" aria-label="Close-up photo of an eye wearing long pink feathered lashes"></div>
<div class="abs hero-title">Tapered in 100% Human Hair</div>
<div class="abs arrow" style="left:79px;background:rgba(255,255,255,.45)"><svg width="8" height="10" viewBox="0 0 8 10"><path d="M6 1L2 5l4 4" fill="none" stroke="#666" stroke-width="1.6"/></svg></div>
<div class="abs arrow" style="left:702px;background:rgba(255,255,255,.6)"><svg width="8" height="10" viewBox="0 0 8 10"><path d="M2 1l4 4-4 4" fill="none" stroke="#333" stroke-width="1.6"/></svg></div>

<h2 class="abs h2" style="left:-3px;top:410px">Welcome To Our Site</h2>
<p class="abs intro">Lorem ipsum dolor sit amet, consectetur adipiscing elit. Aliquam sit amet fringilla est. Praesent nec condimentum lectus. Praesent tempus lacus massa, id tempor urna ele-mentum in. Etiam neque metus, faucibus ut sapien quis, mattis sodales nisi. Etiam non porttitor eros, sed varius quam. Duis semper neque tortor. Pellentesque in nisi varius, hendrerit justo id, laoreet sapien. Aliquam hendrerit urna sed enim tempus mattis. Cum sociis natoque penatibus et magnis dis parturient montes, nascetur ridiculus mus. Donec erat metus, fringilla a odio sed, posuere consectetur nisl. Pellentesque tincidunt eros odio, ac laoreet sapien rutrum iaculis.</p>

<div class="abs features">
  <div class="feature"><svg viewBox="0 0 12 12"><circle cx="6" cy="6" r="6" fill="#222"/><path d="M3 6l2 2 4-4" fill="none" stroke="#fff" stroke-width="1.5"/></svg><span>New Technology With Tapered Hair</span></div>
  <div class="feature"><svg viewBox="0 0 12 12"><circle cx="6" cy="6" r="6" fill="#222"/><path d="M3 6l2 2 4-4" fill="none" stroke="#fff" stroke-width="1.5"/></svg><span>Brand New With Premium Packaging</span></div>
  <div class="feature"><svg viewBox="0 0 12 12"><circle cx="6" cy="6" r="6" fill="#222"/><path d="M3 6l2 2 4-4" fill="none" stroke="#fff" stroke-width="1.5"/></svg><span>Handmade With Premium Hair</span></div>
  <div class="feature"><svg viewBox="0 0 12 12"><circle cx="6" cy="6" r="6" fill="#222"/><path d="M3 6l2 2 4-4" fill="none" stroke="#fff" stroke-width="1.5"/></svg><span>Comportable With Natural And Soft</span></div>
  <div class="feature" style="width:108px"><svg viewBox="0 0 12 12"><circle cx="6" cy="6" r="6" fill="#222"/><path d="M3 6l2 2 4-4" fill="none" stroke="#fff" stroke-width="1.5"/></svg><span>You Look More Perfect With Lumiqa</span></div>
</div>

<h2 class="abs h2" style="left:-3px;top:565px">Our Products</h2>

<div class="abs cards">
  <div class="card rose"><div class="photo" role="img" aria-label="Makeup brush with loose powder" style="background:linear-gradient(135deg,#f4f2f2,#8a7a76 55%,#e8dcdc)"></div><h3>Blosssom Eye’s</h3><span class="more">More</span></div>
  <div class="card magenta"><div class="photo" role="img" aria-label="Assorted nail polish and makeup products" style="background:radial-gradient(circle at 50% 50%,#d4427a,#f2e6ee 60%,#fff)"></div><h3>Blosssom Eye’s</h3><span class="more">More</span></div>
  <div class="card mustard"><div class="photo" role="img" aria-label="Cosmetics collection with brushes and bottles" style="background:linear-gradient(180deg,#fff 30%,#e6a7b8 65%,#c98a4a)"></div><h3>Blosssom Eye’s</h3><span class="more">More</span></div>
  <div class="card sky"><div class="photo" role="img" aria-label="Scattered eye makeup items" style="background:radial-gradient(circle,#b08a6e,#f3efec 55%,#fff)"></div><h3>Blosssom Eye’s</h3><span class="more">More</span></div>
</div>

<div class="abs banner" role="img" aria-label="Banner with close-up of an eye with long lashes"></div>
<p class="abs banner-text">Our Lumiqa products are more special then others. Because we are<br>using new technology with <b>Tapered</b> Hair</p>

<footer class="abs footer"></footer>
<div class="abs fcol" style="left:66px;top:978px"><h4>Shopping with us</h4><ul><li>Why shop with us?</li><li>How it works</li><li>Delivery</li><li>Returns</li><li>Where's my order</li><li>Contact &amp; help</li><li>Wedding list</li><li>Wish lists</li><li>Gift vouchers</li></ul></div>
<div class="abs fcol" style="left:225px;top:980px"><h4>About us</h4><ul><li>Our story</li><li>Customer contact</li><li>Awards</li><li>Press centre</li><li>Work with us</li><li>Terms &amp; conditions</li><li>Privacy &amp; cookies</li></ul></div>
<div class="abs fcol" style="left:359px;top:980px"><h4>Selling with us</h4><ul><li>Why join?</li><li>FAQ's</li><li>Apply to sell with us</li><li>Affiliates</li></ul></div>
<div class="abs fcol" style="left:518px;top:981px"><h4>Signup newsletter</h4></div>
<div class="abs news-input">EMAIL ID</div>
<div class="abs news-btn">SUBSCRIBE NOW</div>
<div class="abs fcol" style="left:518px;top:1100px"><h4>Keep in touch</h4></div>
<div class="abs social">
  <span style="background:#f2a23a"></span><span style="background:#2f4f8f"></span><span style="background:#3aa6e0"></span><span style="background:#fff"></span><span style="background:#3f7fc8"></span>
</div>
<div class="abs rule"></div>
<div class="abs copy">Copyright © 2015yoursite, All right reserved</div>
</body>
</html>
```